Website for International Non-Profit for Birth Parent Searching

LumaKin is a 501(c)(3) non-profit organization that helps Chinese adoptees search and reunite with birth families who were separated due the One Child Policy in China. We want to create a website that can link to an information database that allows website users to easily access information around search ads in an organized way; help connect families to professional searchers; provide resources for community support for adoptees and their families as they embark on a personal and emotional journey of finding birth family through support groups on social media and consultation/education on the searching process; and provide the opportunity for the adoptive community to give back through donations and volunteer opportunities. The final design should foster a sense of community and be easy navigable to access the multiple resources we provide to help families search for each other. We would like to see designs with red/black/white color schemes that are gentle, inviting, and family friendly to viewers. We would like to see some design layouts with Chinese themes, if possible.

```html
<!DOCTYPE html>
<html lang="en">
<head>
<meta charset="utf-8">
<title>LumaKin — Who We Are</title>
<link href="https://fonts.googleapis.com/css2?family=Lato:wght@400;700;900&family=Roboto:wght@400;500;700&display=swap" rel="stylesheet">
<style>
:root{
  --red:#b3121b;
  --red-bright:#d0232a;
  --ink:#111111;
  --text:#333333;
  --white:#ffffff;
  --blush:#f6e0e0;
  --footer:#0b0b0b;
  --field-border:#cfcfcf;
}
*{box-sizing:border-box;margin:0;padding:0}
html,body{width:1200px;height:2957px;overflow:hidden}
body{position:relative;background:var(--white);font-family:"Lato",sans-serif;color:var(--text)}
.abs{position:absolute}

/* header */
.site-header{left:0;top:0;width:1200px;height:90px;background:var(--white);z-index:3}
.brand-badge{left:64px;top:-12px;width:182px;height:185px;border-radius:50%;background:var(--white);z-index:4;display:flex;align-items:center;justify-content:center;padding-top:40px}
.brand-name{font-family:"Lato",sans-serif;font-weight:700;font-size:31px;color:var(--ink)}
.nav-item{top:32px;font-family:"Lato",sans-serif;font-weight:700;font-size:14.5px;letter-spacing:-.4px;color:var(--ink);white-space:nowrap;z-index:4;line-height:18px}
.nav-item.active{color:var(--red)}
.caret{display:inline-block;width:7px;height:7px;border-right:2px solid var(--ink);border-bottom:2px solid var(--ink);transform:rotate(45deg)}
.nav-caret{left:483px;top:34px;z-index:4}
.donate-btn{left:925px;top:21px;width:149px;height:41px;background:var(--red);color:var(--white);font-weight:700;font-size:14px;letter-spacing:-.2px;display:flex;align-items:center;justify-content:center;border-radius:2px;z-index:4}
.lang{left:1094px;top:32px;font-weight:700;font-size:15px;color:var(--ink);z-index:4;line-height:18px}
.lang .caret{width:6px;height:6px;margin-left:10px;border-width:1.5px;position:relative;top:-3px}

/* hero */
.hero-photo{left:0;top:90px;width:1200px;height:400px;background:linear-gradient(100deg,#3d4a1f 0%,#6f7d3a 30%,#a6ad78 50%,#6b7c3b 75%,#2f3d1a 100%)}
.hero-wave{left:0;top:360px;width:1200px;height:130px}

/* who we are */
.section-title{left:0;width:1200px;text-align:center;font-weight:900;font-size:40px;color:var(--ink);letter-spacing:-.5px}
.intro{left:184px;top:622px;width:832px;text-align:center;font-size:16px;line-height:24px;color:var(--text)}
.member-photo{width:254px;height:254px;border-radius:50%;top:825px}
.member-photo::after{content:"";position:absolute;inset:6px;border-radius:50%;border:3px solid var(--white)}
.p1{left:144px;background:radial-gradient(circle at 45% 40%,#d9b9a0 0%,#8a4a28 55%,#4a5a33 100%)}
.p2{left:473px;background:radial-gradient(circle at 50% 40%,#e0b89a 0%,#c46a2b 55%,#6b5a55 100%)}
.p3{left:801px;background:radial-gradient(circle at 50% 40%,#d8b49a 0%,#6c7f9c 55%,#30353d 100%)}
.member{top:1110px;width:320px;text-align:center}
.member h3{font-weight:700;font-size:20px;color:var(--ink)}
.member .role{font-size:15px;margin-top:6px;color:var(--text)}
.member p{font-size:15.5px;line-height:22.4px;margin:20px auto 0;color:var(--text)}
.m1{left:111px}.m1 p{width:232px}
.m2{left:440px}.m2 p{width:310px}
.m3{left:768px}.m3 p{width:250px}

/* banner */
.banner-photo{left:0;top:1485px;width:1200px;height:552px;background:linear-gradient(90deg,#2f4a1c 0%,#5c8a34 40%,#8fbf56 65%,#5a8a2f 85%,#2d4a18 100%)}
.banner-ribbon{left:0;top:1627px;width:630px;height:266px}
.banner-text{left:145px;top:1658px;font-weight:900;font-size:41px;line-height:51px;color:var(--white);letter-spacing:-.5px}

/* contact */
.contact{left:0;top:2037px;width:1200px;height:622px;background:var(--blush)}
.contact-title{left:0;top:2113px;width:1200px;text-align:center;font-weight:900;font-size:34px;color:var(--ink);letter-spacing:-.5px}
.contact-title span{color:var(--red)}
.title-rule{left:563px;top:2168px;width:74px;height:3px;background:var(--red)}
.field{background:var(--white);border:1px solid var(--field-border);box-shadow:0 1px 3px rgba(0,0,0,.18);font-family:"Roboto",sans-serif;font-size:12px;color:#222;padding:0 17px;display:flex;align-items:center}
.field.tall{align-items:flex-start;padding-top:15px}
.submit{left:523px;top:2541px;width:154px;height:39px;background:var(--red);color:var(--white);border-radius:20px;font-family:"Roboto",sans-serif;font-weight:500;font-size:14px;display:flex;align-items:center;justify-content:center}

/* footer */
.site-footer{left:0;top:2659px;width:1200px;height:298px;background:var(--footer)}
.footer-brand{left:130px;top:2760px;width:200px;text-align:center;display:flex;align-items:center;justify-content:center;gap:10px}
.footer-brand .dot{width:14px;height:14px;border-radius:50%;background:var(--red)}
.footer-brand .brand-name{color:var(--white);font-size:34px}
.footer-nav{left:364px;top:2728px;display:flex;gap:27px;font-family:"Roboto",sans-serif;font-weight:500;font-size:13px;color:var(--white);white-space:nowrap}
.footer-rule{left:364px;top:2770px;width:677px;height:1px;background:#8a8a8a}
.contact-item{top:2795px;display:flex;gap:17px;font-family:"Roboto",sans-serif;font-size:14px;line-height:19px;color:var(--white);white-space:nowrap}
.contact-icon{width:29px;height:29px;background:var(--white);display:flex;align-items:center;justify-content:center;flex-shrink:0;margin-top:2px}
.copyright{left:364px;top:2864px;font-family:"Roboto",sans-serif;font-size:10.5px;color:var(--white)}
</style>
</head>
<body>

<header class="abs site-header"></header>
<div class="abs brand-badge"><span class="brand-name">LumaKin</span></div>
<nav>
  <span class="abs nav-item" style="left:304px">HOME</span>
  <span class="abs nav-item active" style="left:376px">WHO WE ARE</span>
  <i class="abs caret nav-caret"></i>
  <span class="abs nav-item" style="left:507px">START YOUR SEARCH</span>
  <span class="abs nav-item" style="left:681px">GET INVOLVED</span>
  <span class="abs nav-item" style="left:811px">RESOURCES</span>
</nav>
<div class="abs donate-btn">DONATE NOW</div>
<div class="abs lang">EN<i class="caret"></i></div>

<div class="abs hero-photo" role="img" aria-label="Three generations of a family walking together along a sunlit park path"></div>
<svg class="abs hero-wave" viewBox="0 0 1200 130" preserveAspectRatio="none" aria-hidden="true">
  <path d="M0 80 C200 35 420 40 620 88 C820 132 1040 110 1200 12 L1200 130 L0 130 Z" fill="#ffffff"/>
  <path d="M0 80 C200 35 420 40 620 88 C820 132 1040 110 1200 12 L1200 2 C1040 104 820 120 620 78 C420 28 200 22 0 64 Z" fill="var(--red)"/>
</svg>

<h1 class="abs section-title" style="top:548px">WHO WE ARE</h1>
<p class="abs intro">Sed ut perspiciatis unde omnis iste natus error sit voluptatem accusantium doloremque laudantium, totam rem aperiam, eaque ipsa quae ab illo inventore veritatis et quasi architecto beatae vitae dicta sunt explicabo. Nemo enim ipsam voluptatem quia voluptas sit aspernatur aut odit aut fugit, sed quia consequuntur magni dolores eos qui ratione voluptatem sequi nesciunt. Neque porro quisquam est, qui dolorem ipsum quia dolor sit amet, consectetur, adipisci velit, sed quia non numquam eius modi tempora incidunt ut labore et dolore magnam aliquam quaerat voluptatem. Ut enim ad minima veniam, quis nostrum exercitationem ullam</p>

<div class="abs member-photo p1" role="img" aria-label="Portrait of the founder smiling while working at a laptop"></div>
<div class="abs member-photo p2" role="img" aria-label="Portrait of a co-founder smiling outdoors"></div>
<div class="abs member-photo p3" role="img" aria-label="Portrait of a co-founder in a blazer with arms crossed"></div>

<div class="abs member m1">
  <h3>Lin Wei</h3>
  <div class="role">(Founder)</div>
  <p>Lin worked for Bright Arc the largest Chinese adoption agency in the world and was the China charity project director for over twenty years. She managed thousands of projects with over hundreds of orphanages in over twenty provinces.</p>
</div>
<div class="abs member m2">
  <h3>Clara Hale Benton</h3>
  <div class="role">(Co-Founder)</div>
  <p>Clara is an adult Chinese adoptee and a Licensed Professional Counselor who understands the complexities that adoption brings around exploring identity, biculturalism, grieving the loss of one’s mother culture and biological family. Clara has done extensive searching for her own birth family and hopes to share the knowledge and hope she has around searching.</p>
</div>
<div class="abs member m3">
  <h3>Nora Whitfield</h3>
  <div class="role">(Co-Founder)</div>
  <p>Nora is a Licensed Professional Counselor whose private practice is about working with adopted and foster children and their families and whose own family includes two children adopted from China. She provided childcare training and ran childcare centers in the orphanages.</p>
</div>

<div class="abs banner-photo" role="img" aria-label="Family with two children walking across a green park lawn under trees"></div>
<svg class="abs banner-ribbon" viewBox="0 0 630 266" preserveAspectRatio="none" aria-hidden="true">
  <path d="M0 0 L627 0 C585 60 575 170 627 266 L0 266 Z" fill="var(--red-bright)" fill-opacity=".95"/>
</svg>
<div class="abs banner-text">WE ARE SEARCHERS.<br>WE ARE PARENTS.<br>WE ARE CHILDREN.<br>WE ARE COMMUNITY.</div>

<section class="abs contact"></section>
<h2 class="abs contact-title">GET <span>IN TOUCH</span></h2>
<div class="abs title-rule"></div>
<div class="abs field" style="left:229px;top:2213px;width:366px;height:44px">First Name</div>
<div class="abs field" style="left:605px;top:2213px;width:367px;height:44px">Last Name</div>
<div class="abs field" style="left:229px;top:2268px;width:366px;height:44px">Email address</div>
<div class="abs field" style="left:605px;top:2268px;width:367px;height:44px">Address</div>
<div class="abs field tall" style="left:229px;top:2325px;width:743px;height:57px">Phone number</div>
<div class="abs field tall" style="left:229px;top:2396px;width:743px;height:113px">Reason for inquiry</div>
<div class="abs submit">SUBMIT</div>

<footer class="abs site-footer"></footer>
<div class="abs footer-brand"><span class="dot"></span><span class="brand-name">LumaKin</span></div>
<nav class="abs footer-nav">
  <span>HOME</span><span>WHO WE ARE</span><span>OUR SERVICES</span><span>GET INVOLVED</span><span>TOOLS AND RESOURCES</span><span>CONTACT US</span>
</nav>
<div class="abs footer-rule"></div>

<div class="abs contact-item" style="left:364px">
  <span class="contact-icon"><svg width="15" height="15" viewBox="0 0 24 24"><path d="M6.6 10.8a15 15 0 006.6 6.6l2.2-2.2c.3-.3.7-.4 1-.2 1.1.4 2.3.6 3.6.6.6 0 1 .4 1 1V20c0 .6-.4 1-1 1A17 17 0 013 4c0-.6.4-1 1-1h3.5c.6 0 1 .4 1 1 0 1.3.2 2.5.6 3.6.1.3 0 .7-.2 1z" fill="var(--red)"/></svg></span>
  <span>Phone:<br>555-010-4421</span>
</div>
<div class="abs contact-item" style="left:533px">
  <span class="contact-icon"><svg width="14" height="17" viewBox="0 0 24 30"><path d="M12 0C5.4 0 0 5.2 0 11.7 0 20 12 30 12 30s12-10 12-18.3C24 5.2 18.6 0 12 0zm0 16a4.5 4.5 0 110-9 4.5 4.5 0 010 9z" fill="var(--red)"/></svg></span>
  <span>2210 Cedar Ridge Lane,<br>4B, Lakemont, CO 80000</span>
</div>
<div class="abs contact-item" style="left:783px">
  <span class="contact-icon"><svg width="16" height="12" viewBox="0 0 24 18"><rect width="24" height="18" rx="1" fill="var(--red)"/><path d="M1 1l11 9 11-9" fill="none" stroke="#fff" stroke-width="2"/></svg></span>
  <span>Email:<br>lumakinfamilies@example.org</span>
</div>
<div class="abs copyright">© COPYRIGHTS 2021 LUMAKIN &nbsp;|&nbsp;&nbsp; ALL RIGHTS RESERVED</div>

</body>
</html>
```